Velk Partners Building Business Cards

We need a business card that reflects our business as "Solar Experts" in San Diego. Browse our website www.velkpartners.example our License needs to be displayed as "CSLB# 3867140" our phone number is (619) 555-0187

Save thousands on your electric bills and increase the value of your home while helping to protect the environment. Our solar installation experts will help you design the system that's right for you, using only the highest quality equipment that will look great and give you ideal performance. Our goal is to make you energy independent, and get your electric bill to 0.

Paul Osterby
(619) 555-0187
paul@velkpartners.example

Target Market(s)

Home owners in san diego looking for solar

Industry/Entity Type

Solar Energy

Contact Information for Business Card

Paul Osterby
(619) 555-0187
paul@velkpartners.example

Font styles to use
Other font styles liked:
• Use our logo font

Requirements
Must have
• License needs to be displayed as "CSLB# 3867140" our phone number is (619) 555-0187
Nice to have
• Real images of rooftop home solar in san diego
Should not have
• our business address

```html
<!DOCTYPE html>
<html lang="en">
<head>
<meta charset="utf-8">
<title>Velk Partners Building – Business Card</title>
<link rel="stylesheet" href="https://fonts.googleapis.com/css2?family=Open+Sans:wght@400;600;700&display=swap">
<style>
  :root {
    --page-bg: #e9e7e4;
    --card-bg: #f7f8fa;
    --navy: #1d2b57;
    --navy-deep: #152046;
    --orange: #e08a1c;
    --orange-light: #f0a43a;
    --contact-text: #e4d7de;
    --title-text: #f1f2f6;
  }
  * { box-sizing: border-box; margin: 0; padding: 0; }
  html, body {
    width: 1200px;
    height: 969px;
    overflow: hidden;
    background: var(--page-bg);
    font-family: "Open Sans", Arial, sans-serif;
  }
  .canvas {
    position: relative;
    width: 1200px;
    height: 969px;
  }
  .business-card {
    position: absolute;
    left: 100px;
    top: 199px;
    width: 1000px;
    height: 572px;
    background: var(--card-bg);
    overflow: hidden;
    box-shadow: 0 10px 30px rgba(0, 0, 0, 0.12);
  }
  .roof-band {
    position: absolute;
    inset: 0;
    width: 100%;
    height: 100%;
  }
  .company-name {
    position: absolute;
    top: 78px;
    left: 0;
    width: 100%;
    display: flex;
    align-items: center;
    justify-content: center;
    gap: 22px;
  }
  .company-mark {
    width: 46px;
    height: 46px;
    border-radius: 50%;
    background: var(--orange);
    flex: none;
  }
  .company-wordmark {
    color: var(--navy);
    font-weight: 700;
    font-size: 56px;
    line-height: 1.05;
    letter-spacing: -0.5px;
  }
  .contact-block {
    position: absolute;
    left: 0;
    top: 360px;
    width: 100%;
    text-align: center;
  }
  .person-name {
    color: var(--orange);
    font-weight: 700;
    font-size: 36px;
    line-height: 1.1;
  }
  .person-title {
    color: var(--title-text);
    font-weight: 400;
    font-size: 26px;
    margin-top: 6px;
  }
  .contact-line {
    color: var(--contact-text);
    font-weight: 400;
    font-size: 27px;
    line-height: 1.55;
  }
  .contact-line:first-of-type { margin-top: 18px; }
</style>
</head>
<body>
<main class="canvas">
  <section class="business-card">
    <svg class="roof-band" viewBox="0 0 1000 572" preserveAspectRatio="none" aria-hidden="true">
      <defs>
        <linearGradient id="navyFill" x1="0" y1="0" x2="0" y2="1">
          <stop offset="0" stop-color="#22336a"/>
          <stop offset="1" stop-color="#152046"/>
        </linearGradient>
        <linearGradient id="orangeFill" x1="0" y1="0" x2="1" y2="0">
          <stop offset="0" stop-color="#c9740f"/>
          <stop offset="0.5" stop-color="#f0a43a"/>
          <stop offset="1" stop-color="#c9740f"/>
        </linearGradient>
      </defs>
      <polygon points="0,408 500,268 1000,408 1000,426 500,292 0,426" fill="url(#orangeFill)"/>
      <polygon points="0,426 500,292 1000,426 1000,572 0,572" fill="url(#navyFill)"/>
    </svg>

    <header class="company-name">
      <span class="company-mark"></span>
      <span class="company-wordmark">Velk Partners<br>Building Inc</span>
    </header>

    <div class="contact-block">
      <p class="person-name">Paul Osterby</p>
      <p class="person-title">CEO/Founder</p>
      <p class="contact-line">CSLB# 3867140 | P : (619) 555-0187</p>
      <p class="contact-line">paul@velkpartners.example | www.velkpartners.example</p>
    </div>
  </section>
</main>
</body>
</html>
```